New Business Card Design Project

Use the flyer uploaded and website www.brightoakbuilders.com for inspiration.
List Our Services on Backside of business cards
Marcus Delling
Harborline Builders Inc.
Licensed General Contractors
858-471-6093

Contact Information for Business Card

Use the flyer uploaded and website www.brightoakbuilders.com for inspiration. List Our Services on Backside of business cards Marcus Delling Harborline Builders Inc. Licensed General Contractors 858-471-6093

```html
<!DOCTYPE html>
<html lang="en">
<head>
<meta charset="utf-8">
<title>Harborline Builders — Business Card</title>
<link href="https://fonts.googleapis.com/css2?family=Montserrat:wght@400;500;700&display=swap" rel="stylesheet">
<style>
  :root {
    --backdrop: #2e2825;
    --card: #1c1c1c;
    --card-back: #121212;
    --ink: #f2f2f2;
    --ink-soft: #cfcfcf;
    --rule: #8a8a8a;
    --pattern-light: #3a3a3a;
    --pattern-dark: #151515;
  }
  * { box-sizing: border-box; margin: 0; padding: 0; }
  html, body { width: 1200px; height: 786px; overflow: hidden; }
  body {
    background: var(--backdrop);
    font-family: "Montserrat", sans-serif;
    color: var(--ink);
    display: flex;
    align-items: center;
    justify-content: center;
    gap: 40px;
  }
  .card {
    width: 540px;
    height: 309px;
    border-radius: 4px;
    position: relative;
    overflow: hidden;
    box-shadow: 0 10px 30px rgba(0,0,0,.45);
  }
  .card--front {
    background: var(--card);
    display: flex;
    align-items: center;
    padding: 0 34px 0 30px;
  }
  .brand {
    width: 220px;
    display: flex;
    align-items: center;
    justify-content: center;
    gap: 10px;
  }
  .brand__mark {
    width: 14px; height: 14px;
    border: 1.5px solid var(--ink);
    flex: none;
  }
  .brand__name {
    font-size: 17px;
    font-weight: 400;
    letter-spacing: 1.5px;
    text-transform: uppercase;
    color: var(--ink);
    line-height: 1.2;
  }
  .divider {
    width: 1px;
    height: 150px;
    background: var(--rule);
    margin: 0 18px 0 12px;
  }
  .contact__name { font-size: 19px; font-weight: 700; line-height: 1.1; }
  .contact__role { font-size: 11px; color: var(--ink-soft); margin-bottom: 14px; }
  .contact__list { list-style: none; font-size: 12px; }
  .contact__list li { display: flex; align-items: center; gap: 10px; margin-bottom: 7px; }
  .contact__list svg { width: 12px; height: 12px; flex: none; }
  .contact__license { font-size: 12px; margin-top: 12px; padding-left: 22px; }

  .card--back { background: var(--card-back); }
  .pattern {
    position: absolute; inset: 0;
    background: linear-gradient(120deg, var(--pattern-light) 0%, var(--pattern-dark) 55%, #1d1d1d 100%);
  }
  .services {
    position: absolute;
    left: 26px; right: 20px; bottom: 30px;
    font-size: 10.5px;
    line-height: 1.9;
    color: var(--ink);
  }
  .services p { white-space: nowrap; }
  .services p:last-child { padding-left: 60px; }
</style>
</head>
<body>

<section class="card card--front">
  <div class="brand">
    <span class="brand__mark"></span>
    <span class="brand__name">Harborline Builders</span>
  </div>
  <div class="divider"></div>
  <div class="contact">
    <h1 class="contact__name">Marcus Delling</h1>
    <p class="contact__role">Managing Director</p>
    <ul class="contact__list">
      <li>
        <svg viewBox="0 0 12 12"><path d="M2.5 1h2l1 3-1.3 1a6 6 0 0 0 2.8 2.8l1-1.3 3 1v2a1 1 0 0 1-1 1A9.5 9.5 0 0 1 1.5 2a1 1 0 0 1 1-1z" fill="#f2f2f2"/></svg>
        858-471-6093
      </li>
      <li>
        <svg viewBox="0 0 12 12"><rect x="0.5" y="2.5" width="11" height="7" fill="#f2f2f2"/><path d="M0.5 2.5 6 6.5l5.5-4" stroke="#1c1c1c" fill="none"/></svg>
        info@brightoakbuilders.com
      </li>
      <li>
        <svg viewBox="0 0 12 12"><circle cx="6" cy="6" r="5.3" fill="none" stroke="#f2f2f2" stroke-width="1.2"/><ellipse cx="6" cy="6" rx="2.2" ry="5.3" fill="none" stroke="#f2f2f2"/><path d="M0.7 6h10.6" stroke="#f2f2f2"/></svg>
        www.brightoakbuilders.com
      </li>
    </ul>
    <p class="contact__license">CSLB Licensed No. #1048261</p>
  </div>
</section>

<section class="card card--back">
  <div class="pattern" role="img" aria-label="Repeating pattern of the company mark in glossy black"></div>
  <div class="services">
    <p>• Remodel: Kitchen &amp; Bath &nbsp;• Painting: Interior &amp; Exterior &nbsp;• Flooring: Carpet, Vinyl, Wood</p>
    <p>• Window/Door Replacement &nbsp;• Plumbing: Repair &amp; Upgrades &nbsp;• Energy Efficient Upgrades</p>
    <p>• Deck &amp; Patio Construction &nbsp;• Water &amp; Mold Damage &nbsp;• Garage Renovation</p>
  </div>
</section>

</body>
</html>
```